Kestrel Facilities Business Card Design

We would now like to design business cards with the new Kestrel Facilities logo

Target Market(s)

Professional

Industry/Entity Type

Professional services

Contact Information for Business Card

Employee name, title, phone number, email address, corporate office address and logo.

Font styles to use
Sans Serif

Colors
0054AA
0677BA
7BADD7
CADEEF
E8F1F8

Requirements
Must have
• My logo
Should not have
• any other pictures or images besides my logo

```html
<!DOCTYPE html>
<html lang="en">
<head>
<meta charset="utf-8">
<title>Kestrel Facilities Business Card</title>
<link rel="stylesheet" href="https://fonts.googleapis.com/css2?family=Montserrat:wght@700&family=Jost:wght@400;500&display=swap">
<style>
  :root {
    --brand-blue: #3677bf;
    --brand-deep: #0054aa;
    --mark-silver: #d3d9e4;
    --faint-blue: #e8f1f8;
    --ink: #1b1b1b;
    --paper: #ffffff;
    --backdrop: #2a2b2e;
  }
  * { box-sizing: border-box; margin: 0; padding: 0; }
  html, body { width: 1200px; height: 900px; overflow: hidden; }
  body {
    background: var(--backdrop);
    font-family: "Jost", sans-serif;
    display: flex;
    flex-direction: column;
    align-items: center;
    justify-content: center;
    gap: 40px;
  }
  .card {
    position: relative;
    width: 700px;
    height: 400px;
    border-radius: 26px;
    overflow: hidden;
  }
  .card-front { background: var(--paper); color: var(--ink); }
  .card-back {
    background: var(--brand-blue);
    display: flex;
    align-items: center;
    justify-content: center;
  }

  .watermark-name {
    position: absolute;
    left: 150px;
    top: 22px;
    font-family: "Jost", sans-serif;
    font-weight: 500;
    font-size: 64px;
    line-height: 1;
    color: var(--faint-blue);
    letter-spacing: 1px;
  }
  .holder {
    position: absolute;
    left: 0;
    top: 100px;
    padding-left: 58px;
  }
  .holder-accent {
    position: absolute;
    left: 26px;
    top: 4px;
    width: 16px;
    height: 30px;
    background: var(--brand-blue);
  }
  .holder-name {
    position: relative;
    font-family: "Montserrat", sans-serif;
    font-weight: 700;
    font-size: 26px;
    color: var(--brand-blue);
    letter-spacing: 0.5px;
  }
  .holder-title {
    position: relative;
    font-size: 19px;
    margin-top: 2px;
    letter-spacing: 0.5px;
  }
  .divider {
    position: absolute;
    left: 40px;
    right: 60px;
    top: 196px;
    height: 2px;
    background: var(--brand-blue);
  }
  .brand-lockup {
    position: absolute;
    right: 60px;
    top: 112px;
    display: flex;
    align-items: center;
    gap: 12px;
  }
  .brand-square {
    width: 26px;
    height: 26px;
    background: var(--brand-blue);
  }
  .brand-name {
    font-family: "Jost", sans-serif;
    font-weight: 500;
    font-size: 34px;
    color: var(--brand-blue);
    letter-spacing: 1px;
  }
  .contact-list {
    position: absolute;
    left: 40px;
    top: 222px;
    list-style: none;
    font-size: 18px;
    line-height: 1.75;
  }
  .contact-list li { display: flex; align-items: center; gap: 12px; }
  .contact-icon { width: 18px; height: 18px; flex: none; }
  .office-address {
    position: absolute;
    right: 60px;
    bottom: 34px;
    text-align: right;
    font-size: 18px;
    line-height: 1.45;
    letter-spacing: 0.5px;
  }

  .back-lockup { display: flex; align-items: center; gap: 20px; }
  .back-square { width: 44px; height: 44px; background: var(--mark-silver); }
  .back-name {
    font-family: "Jost", sans-serif;
    font-weight: 500;
    font-size: 56px;
    color: var(--mark-silver);
    letter-spacing: 2px;
  }
</style>
</head>
<body>
  <section class="card card-front" aria-label="Business card front">
    <div class="watermark-name" aria-hidden="true">Kestrel</div>

    <div class="holder">
      <span class="holder-accent"></span>
      <h1 class="holder-name">AMANI KERUBO</h1>
      <p class="holder-title">Co-Founder</p>
    </div>

    <div class="brand-lockup">
      <span class="brand-square"></span>
      <span class="brand-name">Kestrel Facilities</span>
    </div>

    <div class="divider"></div>

    <ul class="contact-list">
      <li>
        <svg class="contact-icon" viewBox="0 0 24 24" aria-hidden="true">
          <path fill="#3677bf" d="M6.6 10.8a15.1 15.1 0 0 0 6.6 6.6l2.2-2.2a1 1 0 0 1 1-.25 11.4 11.4 0 0 0 3.6.57 1 1 0 0 1 1 1V20a1 1 0 0 1-1 1A17 17 0 0 1 3 4a1 1 0 0 1 1-1h3.5a1 1 0 0 1 1 1c0 1.25.2 2.45.57 3.6a1 1 0 0 1-.25 1z"/>
        </svg>
        +254-700-41125
      </li>
      <li>
        <svg class="contact-icon" viewBox="0 0 24 24" aria-hidden="true">
          <rect x="2" y="5" width="20" height="14" rx="1.5" fill="#3677bf"/>
          <path d="M3 6.5l9 6.5 9-6.5" fill="none" stroke="#fff" stroke-width="1.6"/>
        </svg>
        info@kestrelfacilities.com
      </li>
      <li>
        <svg class="contact-icon" viewBox="0 0 24 24" aria-hidden="true">
          <circle cx="12" cy="12" r="10" fill="#3677bf"/>
          <path d="M2 12h20M12 2c3 3 3 17 0 20M12 2c-3 3-3 17 0 20" fill="none" stroke="#fff" stroke-width="1.4"/>
        </svg>
        www.kestrelfacilities.com
      </li>
    </ul>

    <address class="office-address" style="font-style:normal">
      P.O Box 4410-00100<br>Nairobi, Kenya
    </address>
  </section>

  <section class="card card-back" aria-label="Business card back">
    <div class="back-lockup">
      <span class="back-square"></span>
      <span class="back-name">Kestrel Facilities</span>
    </div>
  </section>
</body>
</html>
```